Upscale business cards needed for Board of Directors

We need professional business cards created for members of our family business Board of Directors. We would like these relatively simple and straightforward, but also with a unique element to set them apart. Probably stick with neutral and simple colors - white, grey etc. We need space for the traditional elements, including name, title, address, email/phone number. And we will be creating several from this template so it needs to be template that is easy to switch information in and out of.
Business
See description

```html
<!DOCTYPE html>
<html lang="en">
<head>
<meta charset="utf-8">
<title>Harbourline Holdings – Business Card</title>
<link href="https://fonts.googleapis.com/css2?family=Arimo:ital,wght@0,400;1,400&display=swap" rel="stylesheet">
<style>
  :root {
    --backdrop: #d6d0c6;
    --card-top: #e4e4e4;
    --card-bottom: #fafafa;
    --ink: #1c1c1c;
    --gold: #a8976e;
    --shadow: rgba(40, 30, 20, 0.25);
  }
  * { box-sizing: border-box; margin: 0; padding: 0; }
  html, body { width: 1200px; height: 892px; overflow: hidden; }
  body {
    background: var(--backdrop);
    font-family: "Arimo", Arial, sans-serif;
    color: var(--ink);
    display: flex;
    align-items: center;
    justify-content: center;
    gap: 48px;
  }
  .card {
    position: relative;
    width: 540px;
    height: 310px;
    border-radius: 18px;
    background: linear-gradient(180deg, var(--card-top) 0%, var(--card-bottom) 100%);
    box-shadow: 0 10px 28px var(--shadow);
  }
  .brand {
    position: absolute;
    left: 0; right: 0;
    display: flex;
    flex-direction: column;
    align-items: center;
  }
  .brand__rule {
    width: 330px;
    height: 4px;
    background: var(--gold);
  }
  .brand__name {
    margin-top: 14px;
    font-size: 30px;
    font-weight: 400;
    color: var(--ink);
    line-height: 1;
    white-space: nowrap;
  }
  .card--front .brand { top: 46px; }
  .card--back .brand { top: 118px; }
  .card--back .brand__rule { width: 380px; }
  .card--back .brand__name { font-size: 36px; margin-top: 16px; }

  .person {
    position: absolute;
    right: 318px;
    top: 162px;
    text-align: right;
    white-space: nowrap;
  }
  .person__name { font-size: 22px; font-weight: 400; }
  .person__title { font-size: 15px; font-style: italic; margin-top: 3px; }

  .divider {
    position: absolute;
    left: 240px;
    top: 148px;
    width: 2px;
    height: 80px;
    background: var(--gold);
  }
  .contact {
    position: absolute;
    left: 258px;
    top: 150px;
    list-style: none;
  }
  .contact__item {
    display: flex;
    align-items: center;
    gap: 12px;
    font-size: 17px;
    height: 25px;
    margin-bottom: 2px;
    white-space: nowrap;
  }
  .contact__icon {
    width: 16px; height: 16px;
    background: var(--gold);
    display: flex; align-items: center; justify-content: center;
    flex: none;
  }
  .contact__icon svg { width: 11px; height: 11px; fill: var(--ink); }
</style>
</head>
<body>
  <section class="card card--front" aria-label="Business card front">
    <div class="brand">
      <div class="brand__rule"></div>
      <p class="brand__name">Harbourline Holdings</p>
    </div>
    <div class="person">
      <p class="person__name">Owen Hartley</p>
      <p class="person__title">Managing Director</p>
    </div>
    <div class="divider"></div>
    <ul class="contact">
      <li class="contact__item">
        <span class="contact__icon"><svg viewBox="0 0 12 12"><path d="M2.5 1h2l1 2.5-1.2 1a6 6 0 0 0 3.2 3.2l1-1.2 2.5 1v2a1 1 0 0 1-1 1A9.5 9.5 0 0 1 1.5 2a1 1 0 0 1 1-1z"/></svg></span>
        021-555-0142
      </li>
      <li class="contact__item">
        <span class="contact__icon"><svg viewBox="0 0 12 12"><path d="M1 3h10v6.5H1z M1.4 3.3 6 6.6l4.6-3.3" stroke="#a8976e" stroke-width="0.8"/></svg></span>
        office@harbourline.com
      </li>
      <li class="contact__item">
        <span class="contact__icon"><svg viewBox="0 0 12 12"><path d="M6 0.8a3.6 3.6 0 0 1 3.6 3.6C9.6 7 6 11.2 6 11.2S2.4 7 2.4 4.4A3.6 3.6 0 0 1 6 0.8zm0 2.2a1.4 1.4 0 1 0 0 2.8 1.4 1.4 0 0 0 0-2.8z"/></svg></span>
        840 N Calder Rd
      </li>
    </ul>
  </section>

  <section class="card card--back" aria-label="Business card back">
    <div class="brand">
      <div class="brand__rule"></div>
      <p class="brand__name">Harbourline Holdings</p>
    </div>
  </section>
</body>
</html>
```